Finding the Root: Reason in Clinical Choice-Crafting

I'd like a cover that looks like it would fit on the shelf next to "The Illness Mirage" by Corwin Talley, "The Close of Forgetting" by Hugh Marchetti, "Meal Mend" by Paul Grieve, "The Energy Restart Plan" by Oscar Pemberley or "The Gland Restart Plan" by the same or "The Cortex Restart Plan" by the same ... either text only (with some interesting fonts that make the title stand out, and the subtitle smaller) or a relevant image, though I'm not entirely sure what that would be since this is a book about big-picture medical decision making.
Author name is Dr Tessa Morrow, NMD
I'll eventually request an e-book, paperback, and audio cover from the winner...

Target Market(s)

practicing physicians

Industry/Entity Type

medicine

Requirements
Must have
• look similar to other books in the genre

```html
<!DOCTYPE html>
<html lang="en">
<head>
<meta charset="UTF-8">
<title>Finding the Root — Book Cover</title>
<link href="https://fonts.googleapis.com/css2?family=Cinzel:wght@400;500&family=Lato:wght@400&display=swap" rel="stylesheet">
<style>
  :root {
    --backdrop: #e6e6e4;
    --paper: #f8f6f2;
    --navy: #153d63;
    --sage: #7a9656;
    --rule: #9fb386;
    --leaf-tone: #b3c49a;
    --node-tone: #9db0c8;
  }
  html, body {
    margin: 0;
    padding: 0;
    width: 1200px;
    height: 1200px;
    overflow: hidden;
    background: var(--backdrop);
  }
  .cover {
    position: absolute;
    left: 233px;
    top: 50px;
    width: 734px;
    height: 1100px;
    background: var(--paper);
  }
  .title { margin: 0; }
  .title-lead,
  .title-main,
  .subtitle-line,
  .author {
    position: absolute;
    left: 0;
    width: 100%;
    margin: 0;
    text-align: center;
    white-space: nowrap;
  }
  .title-lead {
    top: 83px;
    font-family: "Cinzel", serif;
    font-weight: 400;
    font-size: 74px;
    letter-spacing: 0.05em;
    line-height: 1;
    color: var(--navy);
  }
  .title-main {
    top: 183px;
    font-family: "Cinzel", serif;
    font-weight: 400;
    font-size: 212px;
    letter-spacing: 0;
    line-height: 1;
    color: var(--navy);
  }
  .divider,
  .footer-rule {
    position: absolute;
    left: 0;
    width: 100%;
    height: 16px;
  }
  .divider { top: 400px; }
  .footer-rule { top: 1039px; }
  .subtitle-line {
    font-family: "Lato", sans-serif;
    font-weight: 400;
    font-size: 35px;
    letter-spacing: 0.15em;
    line-height: 1;
  }
  .subtitle-line--accent { top: 451px; color: var(--sage); }
  .subtitle-line--base { top: 508px; color: var(--navy); }
  .cover-art {
    position: absolute;
    left: 157px;
    top: 572px;
    width: 410px;
    height: 388px;
    border-radius: 50% 50% 50% 50% / 48% 48% 52% 52%;
    background: linear-gradient(90deg, var(--leaf-tone) 0%, #cdd8bc 48%, #cdd7e3 52%, var(--node-tone) 100%);
    opacity: 0.7;
  }
  .author {
    top: 985px;
    font-family: "Cinzel", serif;
    font-weight: 500;
    font-size: 46px;
    letter-spacing: 0.03em;
    line-height: 1;
    color: var(--navy);
  }
  .author-credential { font-size: 31px; letter-spacing: 0.02em; }
</style>
</head>
<body>
  <main class="cover">
    <h1 class="title">
      <span class="title-lead">FINDING THE</span>
      <span class="title-main">ROOT</span>
    </h1>

    <svg class="divider" viewBox="0 0 734 16" aria-hidden="true">
      <line x1="163" y1="8" x2="341" y2="8" stroke="var(--rule)" stroke-width="1.5"/>
      <circle cx="367" cy="8" r="6" fill="var(--sage)"/>
      <line x1="395" y1="8" x2="570" y2="8" stroke="var(--rule)" stroke-width="1.5"/>
    </svg>

    <p class="subtitle-line subtitle-line--accent">REASON IN CLINICAL</p>
    <p class="subtitle-line subtitle-line--base">CHOICE-CRAFTING</p>

    <div class="cover-art" role="img" aria-label="Illustration of a tree with roots, its left half in green leaves and its right half becoming a blue network of connected nodes"></div>

    <p class="author">DR TESSA MORROW, <span class="author-credential">NMD</span></p>

    <svg class="footer-rule" viewBox="0 0 734 16" aria-hidden="true">
      <line x1="85" y1="8" x2="329" y2="8" stroke="var(--rule)" stroke-width="1.5"/>
      <circle cx="365" cy="8" r="5" fill="var(--sage)"/>
      <line x1="401" y1="8" x2="659" y2="8" stroke="var(--rule)" stroke-width="1.5"/>
    </svg>
  </main>
</body>
</html>
```